Brindlewood Elementary School 2019-2020 Priority Goals

This visual will encapsulate our school's annual goals. We are a large elementary school in a high performing school district. We base our annual goals primarily on our school generated set of foundational promises. We know that the relationships of the people are critical to our success. The product will primarily be used with our staff internally to keep focused on our priority goals for the year, which are to innovate and collaborate. The collaboration is both amongst staff and also in stronger partnerships with our parent community. The innovation is in not settling for how things have always been done and will focus in three areas: future ready skills, academic growth and achievement and finally in social/emotional growth. We have been saying to one another that "we will accelerate the academic and social emotional growth of the students we serve by innovating and collaborating.

Target Market(s)

Staff, parents and school board

Industry/Entity Type

Education

Font styles to use
Other font styles liked:
• open to your ideas

Colors
0255a3
fbed22

Requirements
Must have
• pretty new to this idea, we'll attach the early sketches below. You'll also find a school logo design as well as the promises that are referred to in the sketch.
Nice to have
• the colors below are school colors, but we are open to your creative genius as well.

```html
<!DOCTYPE html>
<html lang="en">
<head>
<meta charset="utf-8">
<title>Brindlewood Elementary School – 2019-2020 Priority Goals</title>
<link href="https://fonts.googleapis.com/css2?family=Oswald:wght@500;600;700&family=Open+Sans:wght@400;600;700&family=Patrick+Hand&display=swap" rel="stylesheet">
<style>
  :root {
    --page-bg: #dfe8f3;
    --header-blue: #2b77c9;
    --title-blue: #1f63c0;
    --yellow: #edc913;
    --mid-blue: #2c78c8;
    --navy: #293b96;
    --footer-navy: #1e3a72;
    --heart-blue: #77abe3;
    --panel-gray: #e4e4e4;
    --white: #ffffff;
  }
  * { margin: 0; padding: 0; box-sizing: border-box; }
  html, body { width: 1200px; height: 1200px; overflow: hidden; background: var(--page-bg); }
  .canvas { position: relative; width: 1200px; height: 1200px; }
  .poster {
    position: absolute; left: 189px; top: 20px;
    width: 884px; height: 1248px;
    transform: scale(0.9295); transform-origin: 0 0;
    background: var(--panel-gray); overflow: hidden;
    font-family: "Open Sans", sans-serif;
  }
  .header { position: absolute; left: 0; top: 0; width: 884px; height: 265px; background: var(--white); }
  .header__title {
    position: absolute; left: 45px; top: 24px;
    font-family: "Oswald", sans-serif; font-weight: 600; font-size: 44px;
    color: var(--title-blue); letter-spacing: 0.5px; transform: scaleX(0.9); transform-origin: left;
  }
  .header__band {
    position: absolute; left: 0; top: 82px; width: 884px; height: 108px; background: var(--header-blue);
  }
  .header__pledge {
    position: absolute; left: 47px; top: 20px; width: 560px;
    color: var(--white); font-weight: 600; font-size: 22px; line-height: 31px;
  }
  .school-mark { position: absolute; left: 620px; top: 18px; width: 250px; height: 236px; }
  .school-mark__disc {
    position: absolute; left: 70px; top: 0; width: 110px; height: 110px;
    border-radius: 50%; background: var(--yellow);
  }
  .school-mark__name {
    position: absolute; left: 0; top: 122px; width: 250px; text-align: center;
    font-family: "Oswald", sans-serif; font-weight: 700; font-size: 27px; line-height: 32px;
    color: var(--navy); text-transform: uppercase;
  }
  .goals-graphic { position: absolute; left: 0; top: 0; }
  .swirl-text {
    position: absolute; font-family: "Patrick Hand", cursive; color: var(--white);
    font-size: 33px; line-height: 38px; letter-spacing: 1px;
  }
  .priority { position: absolute; text-align: center; color: var(--white); font-size: 15px; line-height: 20px; }
  .priority__word {
    font-family: "Oswald", sans-serif; font-weight: 600; font-size: 36px; line-height: 44px;
  }
  .priority__plus { position: absolute; left: 403px; top: 617px; color: var(--white); font-family: "Oswald", sans-serif; font-size: 26px; }
  .focus-list { position: absolute; left: 392px; top: 760px; list-style: none; color: var(--white); font-weight: 700; font-size: 15px; line-height: 20px; }
  .focus-list li::before { content: "✓"; font-weight: 400; margin-right: 6px; font-size: 12px; }
  .footer-title {
    position: absolute; left: 0; top: 1066px; width: 884px; text-align: center;
    font-family: "Oswald", sans-serif; font-weight: 600; font-size: 56px; color: var(--navy);
    transform: scaleX(0.88);
  }
  .footer-stripe { position: absolute; left: 0; top: 1142px; width: 884px; height: 16px; background: var(--yellow); }
  .footer { position: absolute; left: 0; top: 1158px; width: 884px; height: 90px; background: var(--footer-navy); }
  .contact { position: absolute; left: 90px; top: 25px; color: var(--white); font-size: 12px; line-height: 23px; }
  .contact__row { display: flex; align-items: center; gap: 6px; }
  .contact__row svg { flex: none; }
  .contact__gap { display: inline-block; width: 18px; }
  .social { position: absolute; left: 632px; top: 27px; display: flex; gap: 13px; }
  .social__dot { width: 42px; height: 42px; border-radius: 50%; border: 2px solid #c9d6ea; }
  .social__dot--one { background: #213e78; }
  .social__dot--two { background: #1f9ad6; }
  .social__dot--three { background: #5b6fd6; }
</style>
</head>
<body>
<div class="canvas">
  <div class="poster">
    <header class="header">
      <h1 class="header__title">2019-2020 PRIORITY GOALS</h1>
      <div class="header__band">
        <p class="header__pledge">We WILL accelerate the academic, social and emotional growth of the students we serve by:</p>
      </div>
      <div class="school-mark">
        <div class="school-mark__disc"></div>
        <div class="school-mark__name">Brindlewood<br>Elementary School</div>
      </div>
    </header>

    <svg class="goals-graphic" width="884" height="1248" viewBox="0 0 884 1248" aria-hidden="true">
      <path fill="var(--yellow)" d="M107,827 C55,700 68,480 230,370 C350,292 520,290 600,340 C680,392 694,520 672,592 C640,482 560,428 450,432 C360,436 270,470 235,520 C170,600 130,700 107,827 Z"/>
      <path fill="var(--mid-blue)" d="M632,352 C760,430 832,560 807,700 C792,790 760,840 762,862 C690,888 560,896 464,890 C560,850 642,760 652,630 C660,510 650,420 632,352 Z"/>
      <path fill="var(--navy)" d="M242,544 C150,620 112,760 140,870 C180,990 320,1045 450,1037 C580,1030 680,970 722,910 C640,948 540,946 465,930 C340,900 230,810 222,700 C218,630 228,585 242,544 Z"/>
      <path fill="var(--heart-blue)" stroke="var(--panel-gray)" stroke-width="14" d="M443,557 C400,500 300,500 240,530 C200,560 208,640 230,700 C270,790 380,840 457,880 C540,830 640,760 650,640 C656,560 600,510 540,515 C490,520 460,540 443,557 Z"/>
      <g fill="none" stroke="var(--white)" stroke-width="3" stroke-linecap="round">
        <circle cx="327" cy="566" r="16"/>
        <path d="M319,584 v10 h16 v-10 M320,598 h14 M322,603 h10"/>
        <path d="M297,552 l-7,-4 M357,552 l7,-4 M292,570 h-8 M362,570 h8 M327,538 v-8"/>
        <circle cx="520" cy="552" r="12"/><circle cx="552" cy="552" r="12"/>
        <path d="M500,608 v-30 q0,-12 20,-12 q20,0 20,12 v30 M532,608 v-30 q0,-12 20,-12 q20,0 20,12 v30 M500,592 h72"/>
      </g>
      <line x1="294" y1="748" x2="592" y2="748" stroke="var(--white)" stroke-width="3" stroke-dasharray="2 4"/>
    </svg>

    <div class="swirl-text" style="left:227px; top:400px;">Listen!<br>Every student has a song</div>
    <div class="swirl-text" style="left:582px; top:798px;">Marla Quinlan</div>
    <div class="swirl-text" style="left:548px; top:834px;">Relationships</div>
    <div class="swirl-text" style="left:185px; top:851px;">Listening</div>
    <div class="swirl-text" style="left:227px; top:888px;">for every</div>
    <div class="swirl-text" style="left:254px; top:926px;">student’s song</div>

    <div class="priority" style="left:236px; top:618px; width:176px;">
      <div class="priority__word" style="color:#0e4fb5;">INNOVATING</div>
      Agents of Change<br><b>“LEARNERS”</b>
    </div>
    <span class="priority__plus">+</span>
    <div class="priority" style="left:426px; top:618px; width:224px;">
      <div class="priority__word" style="color:#1c2f80;">COLLABORATING</div>
      Staff And Parents<br>Partnership<br><b>“TEAM PLAYERS”</b>
    </div>
    <ul class="focus-list">
      <li>Academic</li>
      <li>Social Emotional</li>
      <li>Future Ready</li>
    </ul>

    <h2 class="footer-title">FOUNDATIONAL BELIEF AND PROMISES</h2>
    <div class="footer-stripe"></div>
    <footer class="footer">
      <div class="contact">
        <div class="contact__row">
          <svg width="10" height="13" viewBox="0 0 10 13"><path fill="var(--yellow)" d="M5,0 a5,5 0 0 1 5,5 c0,3 -5,8 -5,8 s-5,-5 -5,-8 a5,5 0 0 1 5,-5 z"/><circle cx="5" cy="5" r="2" fill="var(--footer-navy)"/></svg>
          1180 Fernhill Ave., Cedar Bend, WA 98000
        </div>
        <div class="contact__row">
          <svg width="12" height="12" viewBox="0 0 12 12"><path fill="var(--yellow)" d="M2,0 l3,3 -1.5,1.5 q1,2.5 4,4 l1.5,-1.5 3,3 -2,2 q-5,0 -10,-10 z"/></svg>
          555-010-3600<span class="contact__gap"></span>
          <svg width="12" height="12" viewBox="0 0 12 12"><rect x="1" y="3" width="10" height="9" rx="1" fill="var(--yellow)"/><rect x="3" y="0" width="6" height="4" fill="var(--yellow)"/></svg>
          555-010-3655
        </div>
      </div>
      <div class="social">
        <div class="social__dot social__dot--one"></div>
        <div class="social__dot social__dot--two"></div>
        <div class="social__dot social__dot--three"></div>
      </div>
    </footer>
  </div>
</div>
</body>
</html>
```